Wordpress template for a mens-choire webpage

Task is to design a Wordpress template for an 98 years old estonian mens choire webpage.
Design should involve details from the attached files, choire logo and the colors of the choire flag: in horizontal orientation bright sky-blue, white, bright grass-green.
Designer signature is allowed to be added to the template, with country of origin.

Reason: Deadline extended 2 days (until 2. March 2014) to accommodate designers creativity.

Thank you everyone for your great designs!
Our project has now entered into a voting and decision phase until 14th of March 2014 (included).

```html
<!DOCTYPE html>
<html lang="en">
<head>
<meta charset="utf-8">
<title>Lindvere Male Choir</title>
<link href="https://fonts.googleapis.com/css2?family=Questrial&family=Dosis:wght@500&family=Nunito:wght@800&family=Lato:wght@400&display=swap" rel="stylesheet">
<style>
:root{
  --header-dark:#1c3a0f;
  --header-mid:#2d5418;
  --flag-green:#5aa123;
  --flag-white:#f2f2f2;
  --flag-blue:#175b9e;
  --accent:#12b4e6;
  --nav-bg:#0c1a07;
  --panel:rgba(10,40,80,.55);
  --frame:#3a3a3a;
  --footer:#050505;
  --text-light:#ffffff;
  --text-muted:#b9c6d6;
  --posted:#7f92a8;
  --brand-ink:#2d5418;
}
*{margin:0;padding:0;box-sizing:border-box}
html,body{width:1200px;height:1192px;overflow:hidden}
body{position:relative;font-family:"Questrial",sans-serif;color:var(--text-light);background:var(--flag-white)}
.flag-bg{position:absolute;left:0;top:0;width:1200px;height:1192px}
.site-header{position:absolute;left:0;top:0;width:1200px;height:124px;background:linear-gradient(180deg,var(--header-dark),var(--header-mid));border-bottom:2px solid #2a6a8a}
.brand{position:absolute;left:182px;top:9px;width:96px;height:106px;background:#fff;border-radius:3px;display:flex;align-items:center;justify-content:center;text-align:center;padding:6px}
.brand-name{font-family:"Questrial",sans-serif;font-size:13px;line-height:1.3;color:var(--brand-ink)}
.main-nav{position:absolute;left:457px;top:60px;display:flex;gap:5px}
.main-nav a{display:block;height:37px;line-height:37px;padding:0 16px;background:var(--nav-bg);color:#fff;font-family:"Lato",sans-serif;font-size:12.5px;text-decoration:none}
.main-nav a.current{background:var(--accent)}
.slider{position:absolute;left:173px;top:162px;width:856px;height:406px;background:var(--frame);padding:8px}
.slide-photo{width:100%;height:100%;background:linear-gradient(180deg,#6a22d8 0%,#5a1cc4 40%,#2a1b4a 70%,#1a1a24 100%)}
.slide-caption{position:absolute;left:26px;top:306px;width:385px;height:48px;background:rgba(18,180,230,.85);font-family:"Dosis",sans-serif;font-weight:500;font-size:29px;line-height:48px;padding-left:17px}
.slide-arrow{position:absolute;top:186px;width:34px;height:34px;background:rgba(0,0,0,.75);display:flex;align-items:center;justify-content:center}
.slide-arrow.prev{left:22px}
.slide-arrow.next{right:22px}
.feature-tile{position:absolute;top:606px;width:264px;height:114px;border:5px solid #555;display:flex;align-items:center;justify-content:center;font-family:"Nunito",sans-serif;font-weight:800;font-size:15.5px;color:#fff;text-decoration:none;text-shadow:0 1px 2px rgba(0,0,0,.6)}
.tile-backstage{left:187px;background:linear-gradient(135deg,#1c8fb8,#35b5d9)}
.tile-events{left:470px;background:linear-gradient(135deg,#2aa0c8,#1f7fb0)}
.tile-videos{left:753px;background:linear-gradient(180deg,#5ecde6,#8ee0ee)}
.recent-posts{position:absolute;left:171px;top:754px;width:858px;height:346px;background:var(--panel)}
.recent-posts h2{position:absolute;left:10px;top:20px;font-weight:400;font-size:20px}
.post{position:absolute;top:64px;width:250px}
.post:nth-of-type(1){left:29px}
.post:nth-of-type(2){left:313px}
.post:nth-of-type(3){left:587px}
.post-thumb{width:227px;height:147px}
.post h3{margin-top:20px;font-weight:400;font-size:13.5px;color:var(--accent)}
.post-date{font-family:"Lato",sans-serif;font-size:10px;color:var(--posted);margin-top:5px}
.post p{font-family:"Lato",sans-serif;font-size:10.3px;line-height:20.5px;color:var(--text-muted);margin-top:2px}
.site-footer{position:absolute;left:0;top:1114px;width:1200px;height:78px;background:var(--footer);border-top:2px solid var(--accent)}
.footer-links{position:absolute;left:178px;top:17px;font-family:"Lato",sans-serif;font-size:10.5px}
.footer-links a{color:#fff;text-decoration:none;padding:0 4px}
.footer-links a:first-child{padding-left:0}
.copyright{position:absolute;left:178px;top:51px;font-family:"Lato",sans-serif;font-size:10px;color:#ccc}
.social{position:absolute;left:753px;top:14px;display:flex;gap:8px}
.social span{width:38px;height:38px;border-radius:50%;border:3px solid #ddd;display:block}
</style>
</head>
<body>
<svg class="flag-bg" viewBox="0 0 1200 1192" aria-hidden="true">
  <rect width="1200" height="1192" fill="var(--flag-white)"/>
  <polygon points="0,124 1200,124 1200,176 0,411" fill="var(--flag-green)"/>
  <polygon points="0,849 1200,561 1200,1192 0,1192" fill="var(--flag-blue)"/>
</svg>

<header class="site-header">
  <div class="brand"><span class="brand-name">Lindvere Male Choir</span></div>
  <nav class="main-nav">
    <a class="current" href="#">HOME</a><a href="#">ABOUT</a><a href="#">EVENTS</a><a href="#">AUDIO</a><a href="#">VIDEO</a><a href="#">BLOG</a><a href="#">CONTACT US</a>
  </nav>
</header>

<section class="slider">
  <div class="slide-photo" role="img" aria-label="Men's choir in dark blazers singing on a purple-lit stage with conductor and pianist"></div>
  <div class="slide-caption">98 Years of Estonian Choire</div>
  <div class="slide-arrow prev"><svg width="12" height="14" viewBox="0 0 12 14"><path d="M9 1 3 7l6 6" stroke="#fff" stroke-width="3" fill="none"/></svg></div>
  <div class="slide-arrow next"><svg width="12" height="14" viewBox="0 0 12 14"><path d="M3 1l6 6-6 6" stroke="#fff" stroke-width="3" fill="none"/></svg></div>
</section>

<a class="feature-tile tile-backstage" href="#" role="img" aria-label="Backstage cables tinted blue">Check Out The Backstage</a>
<a class="feature-tile tile-events" href="#" role="img" aria-label="Concert crowd tinted blue">Check The Events</a>
<a class="feature-tile tile-videos" href="#" role="img" aria-label="Misty winter landscape tinted blue">New Videos</a>

<section class="recent-posts">
  <h2>Recent Posts</h2>
  <article class="post">
    <div class="post-thumb" role="img" aria-label="Boys' choir in red shirts performing outdoors" style="background:linear-gradient(180deg,#b9c2c6,#4f7a3a 55%,#8a2a30)"></div>
    <h3>Lorem ipsum dolor sit amet,</h3>
    <div class="post-date">Posted on : 14.2.2014</div>
    <p>Lorem ipsum dolor sit amet, consectetuer adipiscing elit, sed diam nonummy nibh euismod tincidunt ut laoreet dolore magna aliquam erat volutpat.</p>
  </article>
  <article class="post">
    <div class="post-thumb" role="img" aria-label="Choir in dark blazers on stage" style="background:linear-gradient(180deg,#2b1f22,#1b2133 60%,#0f1420)"></div>
    <h3>Lorem ipsum dolor sit amet,</h3>
    <div class="post-date">Posted on : 14.2.2014</div>
    <p>Lorem ipsum dolor sit amet, consectetuer adipiscing elit, sed diam nonummy nibh euismod tincidunt ut laoreet dolore magna aliquam erat volutpat.</p>
  </article>
  <article class="post">
    <div class="post-thumb" role="img" aria-label="Choir with orchestra in a concert hall" style="background:linear-gradient(180deg,#7a5a4a,#1c1c22 50%,#8a6a48)"></div>
    <h3>Lorem ipsum dolor sit amet,</h3>
    <div class="post-date">Posted on : 14.2.2014</div>
    <p>Lorem ipsum dolor sit amet, consectetuer adipiscing elit, sed diam nonummy nibh euismod tincidunt ut laoreet dolore magna aliquam erat volutpat.</p>
  </article>
</section>

<footer class="site-footer">
  <nav class="footer-links"><a href="#">Site Map</a> | <a href="#">Privacy Policy</a> | <a href="#">Terms &amp; Condition</a> | <a href="#">Contact Us</a></nav>
  <div class="copyright">© 2020. All Rights Reserved</div>
  <div class="social" aria-label="Social links">
    <span style="background:#3b5a9a"></span><span style="background:#2aa3dc"></span><span style="background:#c9302c"></span><span style="background:#d9483b"></span><span style="background:#2a8fc9"></span><span style="background:#c8232c"></span>
  </div>
</footer>
</body>
</html>
```